Website for a financial survey consultancy

WHO WE ARE
We're a niche HR consultancy specialising in salary comparison surveys for the financial asset management industry. We position ourselves as a small, highly responsive organisation with a strong personal relationship with each of our 50+ blue-chip clients.

WHAT WE DO
Our business is 80% surveys (= products), 20% consultancy (= services). The surveys are a set of online products which clients interact with to find the information they are interested in.

WHAT WE WANT
We are completely revising our existing marketing website and need a new up-to-date look and feel for the site. We want you to design 2 web pages
- Home page
- Internal content page

More details below in Must Have Priorities.

REFERENCE SITES
- www.veltramoor.com - nice background image
- www.plimweather.com - ignoring the animations
- www.gasketvale.com
- www.quorbin.com - clean, fresh, styly but prob not corporate enough
- www.dulveropinex.com - spacious, beautiful, slightly dated tho
- www.tambly.co.uk - ignore the colours. Like the simplicity, larger font size (although want to stick with sans-serif fonts for main content)

DELIVERABLES
The final designs should be delivered as one or more PSD files with clearly named layers. All design elements and treatments should be separated out, for example use adjustment layers rather than applied (and subsequently irreversible) adjustments, strokes, shading, etc.

WHAT NEXT
I'll be monitoring the contest every day and can respond to questions fast. You can IM me on Chatterlyne or QBX.

Reason: Hi folks,

I am extending the deadline to this project as I am travelling this week and therefore will not be able to make a final decision until next Monday. I will try and provide further feedback over the course of this week but I am only going to be online occasionally so be prepared to wait a few days for a reply from me.

Thanks for all the designs so far.

Tobias

Target Market(s)

In order of importance, most important first

1. Potential customers - UK & US financial industry HR professionals, short on time. Heard about us already, want to find out more about what we do, confirm relevance for their needs. Core goal - establish credibility: are we properly resourced, will we be around for years to come, are we *real*.

2. Existing customers - UK & US financial industry professionals, short on time, under pressure, want results quickly, minimum faff, expect high quality, slickly presented information. Primary action: login and use surveys.

3. Industry professionals/researchers - probably arriving through blog content, looking to browse and hoover information. Valuable for their ability to spread awareness of who we are amongst their peers.

Industry/Entity Type

Financial

Requirements
Must have
• GENERAL
Style cues - Corporate, professional, financial, stylish, slick, clean, spacious, light
Size - standard 960px grid

NAVIGATION
- [ Home | About us | Surveys | Consulting | Blog ]
- Sub-nav (roll-over dropdown) on About Us, Surveys & Consulting

ALL PAGES
- Site navigation
- Client login (on screen permanently or link to ajaxy in-page pop-up)
- Footer section
- Existing logo (attached)* - this is obviously an important reference point in the design, esp colour

HOME PAGE
- Communicate (link thru to?) survey/consulting split
- Large photo(s)/backdrop (2-3 interchangeable options ideally). Please consider what rights agreement will be necessary for any photos you include in your design.
- Possibly bigger more prominent version of logo
- Strap line/sentence - "Focussed data is the key to success"
- 3 recent blog posts (should look good with and without blog post images)
- Free downloadable PDF research report + supporting blurb

INTERNAL PAGE
- Page title
- Content - typical page will be less than one screenfull
- Level 1 sub-heading
- Level 2 sub-heading
- Bulleted list
- Content supporting image (any image will do - interested in placement, borders (if any), spacing, caption, etc)
- 'Do something' button

* Note: there is some internal debate about this logo at the moment. Some (me) are keen for it to change, some (not me!) are not. If you have an web page design idea/concept that requires an evolution of the logo, go ahead and evolve it. We can explore this further in the design process as necessary, but don't sweat it.
Nice to have
• Values to communicate
- Knowledgeable
- Professional
- Secure
- Personal
- Experienced
- Financial industry specific
- Accurate
- Reliable
Should not have
• - Search box
- Social media links, other than RSS feed button (discrete)

```html
<!DOCTYPE html>
<html lang="en">
<head>
<meta charset="utf-8">
<title>Orvane – HR consultancy</title>
<link rel="stylesheet" href="https://fonts.googleapis.com/css2?family=Arimo:wght@400;700&family=PT+Sans:wght@400;700&display=swap">
<style>
  :root {
    --stage: #333333;
    --brand-red: #6a0c0c;
    --nav-red: rgba(120, 30, 34, 0.88);
    --nav-active: #1d0b0b;
    --ink: #111111;
    --body-text: #333333;
    --panel-bg: rgba(255, 252, 248, 0.88);
    --panel-edge: #e6d8c8;
    --rule-tan: #d4c4b0;
    --footer-bg: #030a0f;
    --footer-link: #efe6d6;
    --footer-small: #c9a97a;
    --pdf-brown: #6a4a3a;
    --arrow-red: #c8320f;
    --white: #ffffff;
  }
  * { box-sizing: border-box; margin: 0; padding: 0; }
  html, body { width: 1200px; height: 900px; overflow: hidden; background: var(--stage); }
  body { position: relative; font-family: "PT Sans", Tahoma, sans-serif; }

  .page { position: absolute; left: 121px; top: 69px; width: 964px; height: 757px; overflow: hidden; }

  .hero-backdrop {
    position: absolute; inset: 0 0 83px 0;
    background:
      linear-gradient(150deg, rgba(255,255,255,0.75) 0%, rgba(240,236,228,0.2) 35%, rgba(255,255,255,0) 60%),
      linear-gradient(180deg, #cfd9e6 0%, #e3e8ee 45%, #eef0f2 75%, #e4e2dc 100%);
  }

  .client-login {
    position: absolute; left: 863px; top: 31px;
    font-size: 12px; color: var(--brand-red); text-decoration: underline;
    font-family: "Arimo", Arial, sans-serif;
  }

  .brand { position: absolute; left: 25px; top: 72px; height: 83px; width: 252px; display: flex; align-items: center; }
  .brand-square { width: 86px; height: 83px; background: var(--brand-red); }
  .brand-name {
    margin-left: 12px; font-family: "Arimo", Arial, sans-serif; font-size: 30px;
    color: var(--brand-red); letter-spacing: -0.5px;
  }

  .main-nav { position: absolute; left: 277px; top: 72px; display: flex; gap: 1px; }
  .main-nav a {
    width: 131px; height: 83px; background: var(--nav-red);
    color: var(--white); text-decoration: none; font-weight: 700; font-size: 12px;
    padding: 0 0 5px 6px; display: flex; align-items: flex-end;
    font-family: "PT Sans", Tahoma, sans-serif; letter-spacing: 0.2px;
  }
  .main-nav a.is-current { background: var(--nav-active); }
  .main-nav a:last-child { width: 135px; }

  .hero-title {
    position: absolute; left: 27px; top: 420px;
    font-family: "Arimo", Arial, sans-serif; font-size: 78px; font-weight: 400;
    color: var(--ink); letter-spacing: -2.5px; line-height: 1;
  }
  .strapline {
    position: absolute; left: 31px; top: 495px;
    font-family: "Arimo", Arial, sans-serif; font-size: 26px; color: var(--brand-red);
    letter-spacing: -0.6px;
  }

  .latest-blogs {
    position: absolute; left: 610px; top: 218px; width: 324px; height: 301px;
    background: var(--panel-bg); border: 3px solid var(--panel-edge); border-radius: 3px;
    padding: 12px 18px 0 18px;
  }
  .latest-blogs h2 {
    font-family: "Arimo", Arial, sans-serif; font-weight: 400; font-size: 21px;
    color: var(--brand-red); letter-spacing: -0.5px; padding-bottom: 7px;
    border-bottom: 5px solid var(--rule-tan); margin-bottom: 9px;
  }
  .blog-post { margin-bottom: 15px; }
  .blog-post p {
    font-size: 11px; font-weight: 700; color: var(--body-text);
    text-align: justify; line-height: 13.5px; margin-bottom: 10px;
  }
  .read-more { font-size: 11px; color: var(--ink); text-decoration: underline; font-family: Tahoma, "PT Sans", sans-serif; }
  .read-more span { color: var(--arrow-red); text-decoration: none; font-weight: 700; font-size: 13px; margin-left: 3px; display: inline-block; }

  .report-download {
    position: absolute; left: 615px; top: 589px; width: 315px; height: 50px;
    background: linear-gradient(180deg, #f6efe6 0%, #e6d7c4 100%);
    border: 2px solid #e0cfb8; border-radius: 3px;
    display: flex; align-items: center; padding-left: 5px; text-decoration: none;
  }
  .report-icon { width: 38px; height: 40px; background: #c4161c; border-radius: 3px; flex: none; }
  .report-text { margin-left: 9px; font-family: "Arimo", Arial, sans-serif; }
  .report-title { display: block; font-size: 18px; color: var(--pdf-brown); letter-spacing: -0.4px; line-height: 19px; }
  .report-sub { display: block; font-size: 12px; color: var(--brand-red); line-height: 13px; }

  .site-footer { position: absolute; left: 0; bottom: 0; width: 964px; height: 83px; background: var(--footer-bg); }
  .footer-nav { position: absolute; left: 23px; top: 26px; display: flex; font-size: 12px; font-family: Tahoma, "PT Sans", sans-serif; }
  .footer-nav a { color: var(--footer-link); text-decoration: none; }
  .footer-nav .sep { color: var(--footer-link); margin: 0 26px; }
  .copyright { position: absolute; left: 23px; top: 48px; font-size: 11px; color: var(--footer-small); font-family: Tahoma, "PT Sans", sans-serif; }
  .footer-brand { position: absolute; left: 787px; top: 17px; display: flex; align-items: center; }
  .footer-brand .brand-square { width: 52px; height: 51px; background: var(--white); }
  .footer-brand .brand-name { font-size: 20px; color: var(--white); margin-left: 8px; }
</style>
</head>
<body>
  <div class="page">
    <div class="hero-backdrop" role="img" aria-label="Photograph of a white arched cable bridge against a pale cloudy sky"></div>

    <a class="client-login" href="#">Client LOGIN</a>

    <div class="brand">
      <div class="brand-square"></div>
      <span class="brand-name">Orvane</span>
    </div>

    <nav class="main-nav">
      <a class="is-current" href="#">HOME</a>
      <a href="#">ABOUT US</a>
      <a href="#">SURVEYS</a>
      <a href="#">CONSULTING</a>
      <a href="#">BLOG</a>
    </nav>

    <h1 class="hero-title">HR consultancy</h1>
    <p class="strapline">Focussed data is the key to success</p>

    <section class="latest-blogs">
      <h2>Latest Blogs</h2>
      <article class="blog-post">
        <p>Lorem ipsum dolor sit amet, consectetur adipiscing elit. Integer fringilla sapien ligula. In hac habitasse platea dictumst.</p>
        <a class="read-more" href="#">Read More</a><span class="read-more"><span>»</span></span>
      </article>
      <article class="blog-post">
        <p>Lorem ipsum dolor sit amet, consectetur adipiscing elit. Integer fringilla sapien ligula. In hac habitasse platea dictumst.</p>
        <a class="read-more" href="#">Read More</a><span class="read-more"><span>»</span></span>
      </article>
      <article class="blog-post">
        <p>Lorem ipsum dolor sit amet, consectetur adipiscing elit. Integer fringilla sapien ligula. In hac habitasse platea dictumst.</p>
        <a class="read-more" href="#">Read More</a><span class="read-more"><span>»</span></span>
      </article>
    </section>

    <a class="report-download" href="#">
      <span class="report-icon"></span>
      <span class="report-text">
        <span class="report-title">Research Report + Supporting Blurb</span>
        <span class="report-sub">Download PDF file</span>
      </span>
    </a>

    <footer class="site-footer">
      <nav class="footer-nav">
        <a href="#">Home</a><span class="sep">|</span>
        <a href="#">about us</a><span class="sep">|</span>
        <a href="#">Surveys</a><span class="sep">|</span>
        <a href="#">Consulting</a><span class="sep">|</span>
        <a href="#">Blog</a>
      </nav>
      <p class="copyright">© 2011 Orvane. All rights reserved</p>
      <div class="footer-brand">
        <div class="brand-square"></div>
        <span class="brand-name">Orvane</span>
      </div>
    </footer>
  </div>
</body>
</html>
```